Business card por a urban DJ, up scale audience target

Need a sober design, modern, conservative colors but i can consider some options, y play rnb, hip hop, EDM and top40.

Business card for contact and personal info, double sided, use logo attrached please; im 42 so i need a card acording to my age an target audience.

Target Market(s)

Adult people, up scale audience

Industry/Entity Type

Music Download

Contact Information for Business Card

Cel (318) 4207265518 www.lumadrift.com

Requirements
Must have
• open mind
Nice to have
• open mind
Should not have
• DJ

```html
<!DOCTYPE html>
<html lang="en">
<head>
<meta charset="utf-8">
<title>LUMA — Business Card</title>
<link rel="stylesheet" href="https://fonts.googleapis.com/css2?family=Roboto:wght@400;700&display=swap">
<style>
  :root {
    --canvas: #e9e7e3;
    --ink: #141414;
    --paper: #ffffff;
    --paper-shade: #e6e6e6;
    --band-dark: #1c1c1c;
    --band-stripe: #9a9a9a;
    --panel-dark: #2b2b2b;
    --panel-mid: #444444;
    --text-light: #f2f2f2;
    --text-grey: #bdbdbd;
    --shadow: rgba(0,0,0,0.28);
  }
  * { margin: 0; padding: 0; box-sizing: border-box; }
  html, body {
    width: 1200px; height: 950px; overflow: hidden;
    background: var(--canvas);
    font-family: "Roboto", Arial, sans-serif;
  }
  .sheet {
    position: relative; width: 1200px; height: 950px;
  }
  .card {
    position: absolute; left: 250px;
    width: 700px; height: 400px;
    overflow: hidden;
    box-shadow: 0 10px 28px var(--shadow);
  }
  .card--front { top: 50px; background: var(--paper); }
  .card--back  { top: 500px; background: var(--ink); }

  .card__art { position: absolute; inset: 0; width: 700px; height: 400px; }

  .brand {
    position: absolute; display: flex; align-items: center; gap: 14px;
    font-weight: 700; letter-spacing: 2px; line-height: 1;
  }
  .brand__mark { display: block; }
  .card--front .brand { left: 56px; top: 54px; font-size: 92px; color: var(--ink); }
  .card--front .brand__mark { width: 22px; height: 22px; background: var(--ink); }
  .card--back .brand { left: 0; right: 0; justify-content: center; top: 126px; font-size: 120px; color: var(--paper-shade); }
  .card--back .brand__mark { width: 28px; height: 28px; background: var(--paper-shade); }

  .contact {
    position: absolute; left: 30px; top: 300px;
    list-style: none; color: var(--text-light); font-size: 19px;
  }
  .contact li { display: flex; align-items: center; gap: 12px; margin-bottom: 10px; }
  .contact svg { width: 18px; height: 18px; flex: none; }

  .person {
    position: absolute; right: 50px; bottom: 36px; text-align: right;
    color: var(--text-grey); text-transform: uppercase;
  }
  .person__name { font-size: 23px; font-weight: 700; letter-spacing: 1px; }
  .person__role { font-size: 19px; letter-spacing: 1px; margin-top: 4px; }

  .back-web {
    position: absolute; left: 0; right: 0; top: 268px; text-align: center;
    color: var(--text-light); font-size: 20px; letter-spacing: 2px;
  }
</style>
</head>
<body>
<main class="sheet">

  <!-- Front side -->
  <section class="card card--front" aria-label="Business card front">
    <svg class="card__art" viewBox="0 0 700 400" aria-hidden="true">
      <defs>
        <linearGradient id="paperFade" x1="0" y1="0" x2="1" y2="0">
          <stop offset="0" stop-color="#ffffff"/>
          <stop offset="1" stop-color="#e4e4e4"/>
        </linearGradient>
        <linearGradient id="panelFade" x1="0" y1="0" x2="0" y2="1">
          <stop offset="0" stop-color="#4a4a4a"/>
          <stop offset="1" stop-color="#262626"/>
        </linearGradient>
      </defs>
      <rect width="700" height="400" fill="url(#paperFade)"/>
      <!-- grey stripe -->
      <polygon points="0,216 432,216 480,262 480,270 428,228 0,228" fill="var(--band-stripe)"/>
      <!-- dark base band -->
      <polygon points="0,234 424,234 470,276 700,276 700,400 0,400" fill="var(--band-dark)"/>
      <!-- right title panel -->
      <rect x="470" y="276" width="230" height="124" fill="url(#panelFade)"/>
    </svg>

    <div class="brand"><span class="brand__mark"></span>LUMA</div>

    <ul class="contact">
      <li>
        <svg viewBox="0 0 18 18" aria-hidden="true"><rect x="4" y="1" width="10" height="16" rx="2" fill="none" stroke="#f2f2f2" stroke-width="1.6"/><circle cx="9" cy="14" r="1" fill="#f2f2f2"/></svg>
        (318) 4207265518
      </li>
      <li>
        <svg viewBox="0 0 18 18" aria-hidden="true"><circle cx="9" cy="9" r="7.5" fill="#f2f2f2"/><path d="M3 9h12M9 1.5c-3 3-3 12 0 15M9 1.5c3 3 3 12 0 15" fill="none" stroke="#1c1c1c" stroke-width="1.2"/></svg>
        www.lumadrift.com
      </li>
    </ul>

    <div class="person">
      <p class="person__name">Marco Vell</p>
      <p class="person__role">President</p>
    </div>
  </section>

  <!-- Back side -->
  <section class="card card--back" aria-label="Business card back">
    <svg class="card__art" viewBox="0 0 700 400" aria-hidden="true">
      <defs>
        <linearGradient id="backFade" x1="0" y1="0" x2="1" y2="0">
          <stop offset="0" stop-color="#1a1a1a"/>
          <stop offset="1" stop-color="#2e2e2e"/>
        </linearGradient>
      </defs>
      <rect width="700" height="400" fill="url(#backFade)"/>
    </svg>
    <div class="brand"><span class="brand__mark"></span>LUMA</div>
    <p class="back-web">LUMADRIFT.COM</p>
  </section>

</main>
</body>
</html>
```